BrimFalcon Business Cards

We have a defined brand. Please visit our website to get a feel for the product and the color pallets. www.brimfalcon-example.com

We need an updated, world class business card design. (See the attached existing card design). Please utilize BOTH sides of the card as shown and be creative with the layout. I do want the horse head icon to be positioned as it is with the existing card.

The remainder of the layout can be customized and I also want it vertically oriented.

Attached are the logo files and please use the colors as follows:
Green - #A5CE39
Tan - #CDBD99
Black

Feel free to play with the colors.

```html
<!DOCTYPE html>
<html lang="en">
<head>
<meta charset="utf-8">
<title>BrimFalcon Business Cards</title>
<link rel="stylesheet" href="https://fonts.googleapis.com/css2?family=Poppins:wght@300;400;500&display=swap">
<style>
  :root {
    --stage: #bdbdbd;
    --card-black: #1c1c1c;
    --green: #a5ce39;
    --tan: #d6c7a4;
    --tan-light: #e3d7b9;
    --ink: #1a1a1a;
    --white: #f2f2f2;
  }
  * { margin: 0; padding: 0; box-sizing: border-box; }
  html, body { width: 1200px; height: 876px; overflow: hidden; }
  body {
    background: var(--stage);
    font-family: "Poppins", sans-serif;
    position: relative;
  }
  .card {
    position: absolute;
    top: 138px;
    width: 350px;
    height: 600px;
    border-radius: 14px;
    overflow: hidden;
  }
  .card--front { left: 220px; background: var(--card-black); }
  .card--back { left: 630px; background: linear-gradient(160deg, var(--tan-light), var(--tan)); }

  .emblem-area {
    position: absolute;
    left: 30px; top: 40px;
    width: 290px; height: 300px;
    border-radius: 50%;
  }
  .card--front .emblem-area {
    background: radial-gradient(circle at 50% 45%, #2a2a2a, var(--card-black) 70%);
  }
  .card--back .emblem-area {
    left: 25px; top: 30px; width: 300px; height: 340px;
    background: radial-gradient(circle at 50% 45%, #ece2c9, var(--tan-light) 70%);
  }

  .identity { position: absolute; left: 36px; top: 350px; right: 20px; }
  .identity__name { color: var(--green); font-weight: 400; font-size: 40px; line-height: 1.1; white-space: nowrap; }
  .identity__title { color: var(--white); font-weight: 300; font-size: 22px; margin-top: 2px; }

  .contact { position: absolute; left: 36px; top: 456px; right: 14px; list-style: none; }
  .contact__item {
    display: flex; align-items: center; gap: 10px;
    color: var(--white); font-weight: 300; font-size: 15px; line-height: 24px;
    white-space: nowrap;
  }
  .contact__item--location { color: var(--green); margin-bottom: 12px; }
  .contact__icon { width: 13px; height: 13px; flex: none; }

  .wordmark {
    position: absolute;
    right: 26px; bottom: 34px;
    display: flex; align-items: center; gap: 12px;
    writing-mode: vertical-rl;
    transform: rotate(180deg);
    white-space: nowrap;
  }
  .wordmark__dot { width: 30px; height: 30px; border-radius: 50%; background: var(--ink); }
  .wordmark__name { color: var(--ink); font-weight: 500; font-size: 30px; letter-spacing: 0.5px; line-height: 1; }
</style>
</head>
<body>
  <section class="card card--front" aria-label="Business card front">
    <div class="emblem-area" role="img" aria-label="Faint brand emblem decoration"></div>
    <div class="identity">
      <h1 class="identity__name">Dana Merrow</h1>
      <p class="identity__title">President &amp; CEO</p>
    </div>
    <ul class="contact">
      <li class="contact__item contact__item--location">
        <svg class="contact__icon" viewBox="0 0 14 14"><path d="M7 1a4.5 4.5 0 0 0-4.5 4.5C2.5 9 7 13 7 13s4.5-4 4.5-7.5A4.5 4.5 0 0 0 7 1zm0 6.2a1.7 1.7 0 1 1 0-3.4 1.7 1.7 0 0 1 0 3.4z" fill="#a5ce39"/></svg>
        Northvale, Prairie Province
      </li>
      <li class="contact__item">
        <svg class="contact__icon" viewBox="0 0 14 14"><path d="M3 1.5l2 2.5-1.2 1.5a7 7 0 0 0 4.7 4.7L10 9l2.5 2-1.3 2C6 13 1 8 1 2.8z" fill="#a5ce39"/></svg>
        555.014.2290
      </li>
      <li class="contact__item">
        <svg class="contact__icon" viewBox="0 0 14 14"><rect x="1" y="3" width="12" height="8.5" fill="#a5ce39"/><path d="M1 3l6 5 6-5" stroke="#1c1c1c" stroke-width="1.2" fill="none"/></svg>
        www.brimfalcon-example.com
      </li>
      <li class="contact__item">
        <svg class="contact__icon" viewBox="0 0 14 14"><rect x="1" y="3" width="12" height="8.5" fill="#a5ce39"/><path d="M1 3l6 5 6-5" stroke="#1c1c1c" stroke-width="1.2" fill="none"/></svg>
        dana@brimfalcon-example.com
      </li>
    </ul>
  </section>

  <section class="card card--back" aria-label="Business card back">
    <div class="emblem-area" role="img" aria-label="Embossed brand emblem decoration"></div>
    <div class="wordmark">
      <span class="wordmark__dot"></span>
      <span class="wordmark__name">BrimFalcon Labs</span>
    </div>
  </section>
</body>
</html>
```